Marlowe Group needs a business card

I would like the card to be simple but modern and elegant.
I like black and white.
or black and gold.
we are a private finance lender and also are involved in property and property developments.

please look at the business card photos i provided i would like M.G only one one side and all the other details on the other side use fonts that tie in with my theme.

Industry/Entity Type

Finance

Contact Information for Business Card

Marlowe Group (M.G) Daniel Marlowe M: 0413586207 E: danmarl@inboxmail.test

Font styles to use
Other font styles liked:
• Use fonts that would reflect our business

Colors
000000
ffffff

Requirements
Must have
• one side of details
• other side has either M.G or Marlowe Group like in the photos provided

```html
<!DOCTYPE html>
<html lang="en">
<head>
<meta charset="UTF-8">
<title>Marlowe Group – Business Card</title>
<link rel="stylesheet" href="https://fonts.googleapis.com/css2?family=Cinzel:wght@400&family=Lato:wght@400;700&display=swap">
<style>
  :root {
    --page-bg: #ecebea;
    --card-black: #000000;
    --gold-light: #fde78f;
    --gold-deep: #f0c236;
    --gold-text: #f2c335;
    --ink: #111111;
  }
  * { margin: 0; padding: 0; box-sizing: border-box; }
  html, body {
    width: 1200px;
    height: 900px;
    overflow: hidden;
    background: var(--page-bg);
  }
  .canvas {
    position: relative;
    width: 1200px;
    height: 900px;
  }
  .card {
    position: absolute;
    background: var(--card-black);
    overflow: hidden;
    box-shadow: 0 6px 18px rgba(0,0,0,0.18);
  }

  /* Details side */
  .card--details {
    left: 78px;
    top: 34px;
    width: 588px;
    height: 364px;
  }
  .details-panel {
    position: absolute;
    left: 0;
    top: 0;
    width: 268px;
    height: 100%;
    background: linear-gradient(180deg, var(--gold-light) 0%, #fbdc78 55%, var(--gold-deep) 100%);
    padding: 126px 0 0 29px;
    font-family: "Lato", sans-serif;
    color: var(--ink);
  }
  .holder-name {
    font-weight: 700;
    font-size: 21px;
    letter-spacing: 0.1px;
    margin-bottom: 40px;
  }
  .contact-list { list-style: none; }
  .contact-item {
    display: flex;
    align-items: center;
    gap: 9px;
    font-size: 15px;
    line-height: 25px;
  }
  .contact-icon { width: 11px; height: 11px; flex: none; }
  .brand-panel {
    position: absolute;
    left: 268px;
    top: 0;
    right: 0;
    bottom: 0;
    display: flex;
    align-items: center;
    justify-content: center;
  }
  .brand-name {
    font-family: "Cinzel", serif;
    font-weight: 400;
    color: var(--gold-text);
    font-size: 26px;
    letter-spacing: 0.5px;
  }

  /* Brand side */
  .card--brand {
    left: 388px;
    top: 505px;
    width: 567px;
    height: 352px;
  }
  .gold-band {
    position: absolute;
    top: 82px;
    height: 188px;
    background: linear-gradient(180deg, var(--gold-light) 0%, #fbdc78 50%, var(--gold-deep) 100%);
  }
  .gold-band--left { left: 0; width: 153px; }
  .gold-band--right { left: 417px; width: 150px; }
  .brand-center {
    position: absolute;
    left: 153px;
    width: 264px;
    top: 82px;
    height: 188px;
    display: flex;
    align-items: center;
    justify-content: center;
  }
  .brand-center .brand-name { font-size: 25px; }
</style>
</head>
<body>
<main class="canvas">

  <section class="card card--details" aria-label="Business card, details side">
    <div class="details-panel">
      <h1 class="holder-name">Daniel Marlowe</h1>
      <ul class="contact-list">
        <li class="contact-item">
          <svg class="contact-icon" viewBox="0 0 24 24" aria-hidden="true">
            <path fill="#111" d="M6.6 10.8a15.1 15.1 0 0 0 6.6 6.6l2.2-2.2a1 1 0 0 1 1-.25 11.4 11.4 0 0 0 3.6.57 1 1 0 0 1 1 1V20a1 1 0 0 1-1 1A17 17 0 0 1 3 4a1 1 0 0 1 1-1h3.5a1 1 0 0 1 1 1c0 1.25.2 2.45.57 3.57a1 1 0 0 1-.25 1z"/>
          </svg>
          <span>0413586207</span>
        </li>
        <li class="contact-item">
          <svg class="contact-icon" viewBox="0 0 24 24" aria-hidden="true">
            <path fill="#111" d="M2 5h20v14H2z"/>
            <path fill="none" stroke="#fbdc78" stroke-width="2" d="M3 6l9 7 9-7"/>
          </svg>
          <span>danmarl@inboxmail.test</span>
        </li>
      </ul>
    </div>
    <div class="brand-panel">
      <span class="brand-name">Marlowe Group</span>
    </div>
  </section>

  <section class="card card--brand" aria-label="Business card, brand side">
    <div class="gold-band gold-band--left"></div>
    <div class="brand-center">
      <span class="brand-name">Marlowe Group</span>
    </div>
    <div class="gold-band gold-band--right"></div>
  </section>

</main>
</body>
</html>
```